Corporate Business Card

Very professional, Modern, Not to busy, include phone address email, website
(253) 617-4930, 18761 52nd Avenue S, Kent, WA 98047, martin@plumlinegroup.com, varkoworks.com

Target Market(s)

Manufacturing

Industry/Entity Type

Aero, machining, manufacturing, Off road racing

Contact Information for Business Card

Phone, address email, website

```html
<!DOCTYPE html>
<html lang="en">
<head>
<meta charset="utf-8">
<title>Varko Works – Business Card</title>
<link rel="stylesheet" href="https://fonts.googleapis.com/css2?family=Roboto:wght@400;500&family=Saira:wght@600;700&display=swap">
<style>
  :root {
    --backdrop: #2a2a2a;
    --navy: #2c3a6c;
    --navy-deep: #263460;
    --red: #bf2126;
    --red-deep: #a81d22;
    --white: #ffffff;
    --steel: #1c1f2a;
    --rule: #15182a;
  }
  html, body {
    margin: 0;
    width: 1200px;
    height: 1138px;
    overflow: hidden;
    background: var(--backdrop);
  }
  .card {
    position: absolute;
    border-radius: 14px;
    overflow: hidden;
    background: linear-gradient(180deg, var(--navy) 0%, var(--navy-deep) 100%);
  }
  .card-front { left: 274px; top: 186px; width: 623px; height: 376px; }
  .card-back  { left: 276px; top: 608px; width: 618px; height: 374px; }

  .front-mark {
    position: absolute;
    left: 0; right: 0; top: 98px;
    text-align: center;
    font-family: 'Saira', sans-serif;
    font-weight: 700;
    color: var(--steel);
  }
  .front-mark .brand-name { font-size: 84px; line-height: 1; letter-spacing: 2px; }
  .front-mark .brand-sub {
    position: absolute;
    left: 105px; right: 105px; top: 96px;
    display: flex; align-items: center; gap: 18px;
    font-size: 26px; line-height: 1;
  }
  .front-mark .brand-rule { flex: 1; height: 2px; background: var(--rule); }

  .front-web {
    position: absolute;
    left: 0; right: 0; top: 326px;
    text-align: center;
    font-family: 'Roboto', sans-serif;
    font-size: 16px;
    letter-spacing: 9.5px;
    color: var(--white);
  }
  .front-web .accent { color: var(--red); }

  .back-art { position: absolute; inset: 0; }

  .contact {
    position: absolute;
    left: 66px; top: 104px;
    font-family: 'Roboto', sans-serif;
    color: var(--white);
  }
  .contact-name {
    margin: 0 0 14px;
    font-family: 'Saira', sans-serif;
    font-weight: 700;
    font-size: 25px;
    letter-spacing: 0.5px;
    line-height: 1;
  }
  .contact-name .last { color: var(--red); }
  .contact-list { list-style: none; margin: 0; padding: 0; font-size: 17px; line-height: 24.4px; }
  .contact-list li { display: flex; }
  .contact-list .icon { width: 32px; flex: none; display: flex; align-items: center; }
  .contact-list .icon svg { width: 13px; height: 13px; fill: var(--red); }
</style>
</head>
<body>

<section class="card card-front">
  <div class="front-mark">
    <div class="brand-name">VARKO</div>
    <div class="brand-sub"><span class="brand-rule"></span><span>Works</span></div>
  </div>
  <div class="front-web">www.varko<span class="accent">works</span>.com</div>
</section>

<section class="card card-back">
  <svg class="back-art" width="618" height="374" viewBox="0 0 618 374">
    <defs>
      <linearGradient id="redPanel" x1="0" y1="0" x2="0" y2="1">
        <stop offset="0" stop-color="#c42328"/>
        <stop offset="1" stop-color="#a81d22"/>
      </linearGradient>
    </defs>
    <path d="M458 0 Q318 187 452 374 L618 374 L618 0 Z" fill="#e9e9ec"/>
    <path d="M462 0 Q330 187 468 374 L618 374 L618 0 Z" fill="url(#redPanel)"/>
    <g font-family="Saira, sans-serif" font-weight="700" fill="#ffffff">
      <text transform="translate(528 192) rotate(-90)" text-anchor="middle" font-size="60">VARKO</text>
      <text transform="translate(567 148) rotate(-90)" text-anchor="middle" font-size="22">Works</text>
    </g>
    <line x1="560" y1="196" x2="560" y2="326" stroke="#ffffff" stroke-width="1.5"/>
  </svg>

  <div class="contact">
    <h1 class="contact-name">MARTIN <span class="last">HALE</span></h1>
    <ul class="contact-list">
      <li><span class="icon"><svg viewBox="0 0 16 16"><path d="M2 6c0-2 3-4 6-4s6 2 6 4v1h-3V5.5H5V7H2z M4 8h8l2 6H2z"/></svg></span>(253) 617-4930</li>
      <li><span class="icon"><svg viewBox="0 0 16 16"><path d="M1 3h14v10H1z M2 4l6 5 6-5" stroke="#2c3a6c" stroke-width="1"/></svg></span>martin@plumlinegroup.com</li>
      <li><span class="icon"><svg viewBox="0 0 16 16"><path d="M8 0a5.5 5.5 0 0 0-5.5 5.5C2.5 10 8 16 8 16s5.5-6 5.5-10.5A5.5 5.5 0 0 0 8 0zm0 7.8a2.3 2.3 0 1 1 0-4.6 2.3 2.3 0 0 1 0 4.6z"/></svg></span>18761 52nd Avenue S,</li>
      <li><span class="icon"></span>Kent, WA 98047</li>
      <li><span class="icon"><svg viewBox="0 0 16 16"><circle cx="8" cy="8" r="7"/><path d="M1 8h14M8 1v14M3 4h10M3 12h10" stroke="#2c3a6c" stroke-width="1" fill="none"/></svg></span>www.varkoworks.com</li>
    </ul>
  </div>
</section>

</body>
</html>
```